Business Card Design Project

This is the first time we use our new logo. We need a business card that we can use both on our institutional corporate relationships and also that works for our staff that deals with consumers directly.

VELUNDA is a new company dedicated to empower consumers and to provide them with the best choices for specialized health care using the latest telemedicine technology (medicine at a distance via videoconference).

We want to print this cards in high quality materials and process. We will like designs that allow us to use UV spot varnish and other techniques that will differentiate us.

We are including Two different versions of Color logos. In addition we are including white over black background logos. Those can be used replacing the black for a color.

Please note this is the first time we will be creating any corporate materials with our new logo and colors.

Target Market(s)

34+ consumers of medium high and high socioeconomic levels.

Industry/Entity Type

Health

Requirements
Must have
• Our logo on its original colors
Should not have
• Any other graphical element or design that is not our logo

```html
<!DOCTYPE html>
<html lang="en">
<head>
<meta charset="utf-8">
<title>VELUNDA Business Card</title>
<link rel="stylesheet" href="https://fonts.googleapis.com/css2?family=Montserrat:wght@600;700&family=Arimo:wght@400&display=swap">
<style>
  :root {
    --navy: #1b5a85;
    --teal: #17a39a;
    --sky: #58b4dd;
    --white: #ffffff;
    --ink: #222222;
    --rule: #d9d9d9;
    --backdrop: #eeeae5;
  }
  * { margin: 0; padding: 0; box-sizing: border-box; }
  html, body { width: 1200px; height: 1057px; overflow: hidden; }
  body { background: var(--backdrop); position: relative; font-family: "Arimo", Arial, sans-serif; }

  .card { position: absolute; width: 640px; height: 366px; box-shadow: 0 6px 18px rgba(0,0,0,0.18); overflow: hidden; }

  /* Front */
  .card-front { left: 80px; top: 90px; background: var(--white); }
  .front-brand { position: absolute; left: 34px; top: 160px; width: 286px; display: flex; align-items: center; gap: 12px; white-space: nowrap; }
  .brand-dot { width: 26px; height: 26px; border-radius: 50%; background: var(--navy); flex: none; }
  .brand-name { font-family: "Montserrat", Arial, sans-serif; font-weight: 700; font-size: 36px; letter-spacing: 2px; color: var(--navy); line-height: 1; }
  .divider { position: absolute; left: 340px; top: 26px; width: 1px; height: 230px; background: var(--rule); }
  .contact { position: absolute; left: 372px; top: 36px; color: var(--ink); }
  .person-name { font-family: "Montserrat", Arial, sans-serif; font-weight: 700; font-size: 27px; color: var(--navy); line-height: 1.1; }
  .person-title { font-size: 19px; color: var(--teal); margin-bottom: 18px; }
  .contact-line { display: flex; align-items: center; gap: 8px; font-size: 16px; line-height: 24px; }
  .contact-line svg { width: 14px; height: 14px; fill: var(--navy); flex: none; }
  .address { margin-top: 18px; font-size: 16px; line-height: 20px; }
  .front-band { position: absolute; left: 0; right: 0; bottom: 0; height: 66px; background: var(--navy); border-top: 3px solid var(--white); box-shadow: 0 -2px 0 var(--teal); }
  .front-url { position: absolute; right: 60px; top: 18px; color: var(--white); font-size: 21px; letter-spacing: 5px; }

  /* Back */
  .card-back { left: 480px; top: 590px; background: var(--sky); }
  .back-brand { position: absolute; left: 0; right: 0; top: 120px; display: flex; justify-content: center; align-items: center; gap: 16px; white-space: nowrap; }
  .back-brand .brand-dot { background: var(--white); width: 40px; height: 40px; }
  .back-brand .brand-name { color: var(--white); font-size: 52px; letter-spacing: 3px; }
  .back-url { position: absolute; left: 0; right: 0; top: 262px; text-align: center; color: var(--white); font-size: 23px; letter-spacing: 6px; }
</style>
</head>
<body>
  <section class="card card-front">
    <div class="front-brand">
      <span class="brand-dot"></span>
      <span class="brand-name">VELUNDA</span>
    </div>
    <div class="divider"></div>
    <div class="contact">
      <p class="person-name">Your Name</p>
      <p class="person-title">Title</p>
      <p class="contact-line">
        <svg viewBox="0 0 16 16" aria-hidden="true"><path d="M3.6 1.2l2.3 2.6-1.2 1.8c.9 2 2.4 3.6 4.6 4.7l1.8-1.2 2.6 2.3-1.3 2.6C7.3 13.7 2.3 8.7 1 3.6z"/></svg>
        012-555-0190
      </p>
      <p class="contact-line">
        <svg viewBox="0 0 16 16" aria-hidden="true"><path d="M3.6 1.2l2.3 2.6-1.2 1.8c.9 2 2.4 3.6 4.6 4.7l1.8-1.2 2.6 2.3-1.3 2.6C7.3 13.7 2.3 8.7 1 3.6z"/></svg>
        012-555-0190
      </p>
      <p class="contact-line">
        <svg viewBox="0 0 16 16" aria-hidden="true"><path d="M1 3h14v10H1z M2 4l6 5 6-5" fill="none" stroke="#1b5a85" stroke-width="1.6"/></svg>
        name@velunda.com
      </p>
      <p class="address">Street Name, City Name<br>State, City Zip Code</p>
    </div>
    <div class="front-band"><span class="front-url">www.velunda.com</span></div>
  </section>

  <section class="card card-back">
    <div class="back-brand">
      <span class="brand-dot"></span>
      <span class="brand-name">VELUNDA</span>
    </div>
    <p class="back-url">www.velunda.com</p>
  </section>
</body>
</html>
```